Custom unique Stationary design for Logistics company

We need a custom, unique , elegant and luxurious full stationary design using our new logo, following these guidelines:
1- Business card: double sided, both sides uses the navy blue as the background main color (same as the code of the navy blue used in our logo).
2- envelope and folder: also use the same navy blue as the main background color.
3- book cover( notepad cover) : same thing with the navy blue
4- letterhead: feel free to use the combination of the colors in our logo.
5- rest of the items are up to your creativity

Target Market(s)

corporates and other businesses

Industry/Entity Type

Logistics and heavy machines contractors

Requirements
Must have
• Letterhead, business card, envelope, notepad cover, paper, file
Nice to have
• navy blue to be main background color for business card, envelope, notepad cover

```html
<!DOCTYPE html>
<html lang="en">
<head>
<meta charset="utf-8">
<title>Northvale Cargo – Envelope</title>
<link rel="stylesheet" href="https://fonts.googleapis.com/css2?family=Montserrat:wght@500;800&display=swap">
<style>
  :root {
    --navy: #064c70;
    --orange: #e85c2f;
    --paper: #f6f5f5;
    --backdrop: #d0cfcf;
    --ink: #1d1d1f;
  }
  html, body {
    margin: 0;
    padding: 0;
    overflow: hidden;
  }
  body {
    width: 1200px;
    height: 1050px;
    background: var(--backdrop);
    position: relative;
    font-family: "Montserrat", sans-serif;
  }
  .envelope {
    position: absolute;
    left: 145px;
    width: 910px;
    height: 390px;
    background: var(--paper);
    overflow: hidden;
  }
  .envelope--back { top: 105px; }
  .envelope--front { top: 555px; }
  .envelope svg.art {
    position: absolute;
    inset: 0;
  }
  .flap-brand {
    position: absolute;
    top: 0;
    left: 0;
    width: 910px;
    height: 131px;
    display: flex;
    align-items: center;
    justify-content: center;
    gap: 10px;
  }
  .brand-name {
    font-weight: 800;
    letter-spacing: 0.02em;
    text-transform: uppercase;
    line-height: 1;
    margin: 0;
  }
  .flap-brand .brand-name {
    color: #ffffff;
    font-size: 38px;
  }
  .brand-dot {
    width: 14px;
    height: 14px;
    border-radius: 50%;
    background: #ffffff;
  }
  .front-brand {
    position: absolute;
    left: 42px;
    top: 70px;
    display: flex;
    align-items: center;
    gap: 12px;
  }
  .front-brand .brand-name {
    color: var(--navy);
    font-size: 46px;
  }
  .front-brand .brand-dot {
    width: 20px;
    height: 20px;
    background: var(--orange);
  }
  .return-address {
    position: absolute;
    left: 41px;
    top: 185px;
    margin: 0;
    font-style: normal;
    font-weight: 500;
    font-size: 15px;
    line-height: 20px;
    color: var(--ink);
  }
</style>
</head>
<body>

  <section class="envelope envelope--back" aria-label="Envelope back">
    <svg class="art" width="910" height="390" viewBox="0 0 910 390" aria-hidden="true">
      <path class="flap" fill="var(--navy)"
            d="M0,0 L910,0 L885,91 C876,116 858,131 834,131 L76,131 C52,131 34,116 25,91 Z"/>
    </svg>
    <div class="flap-brand">
      <span class="brand-dot"></span>
      <p class="brand-name">Northvale Cargo</p>
    </div>
  </section>

  <section class="envelope envelope--front" aria-label="Envelope front">
    <svg class="art" width="910" height="390" viewBox="0 0 910 390" aria-hidden="true">
      <path class="wave-accent" fill="var(--orange)"
            d="M0,316 C60,275 130,256 200,256 C420,256 560,330 720,330 C820,330 870,300 910,260
               L910,271 C870,313 820,342 720,342 C560,342 420,268 200,268 C130,268 60,286 0,322 Z"/>
      <path class="wave-base" fill="var(--navy)"
            d="M0,326 C60,290 130,278 200,278 C400,278 550,350 720,352 C820,353 880,320 910,285 L910,390 L0,390 Z"/>
    </svg>
    <div class="front-brand">
      <span class="brand-dot"></span>
      <p class="brand-name">Northvale Cargo</p>
    </div>
    <address class="return-address">
      1420 Harbour Lane, Unit 118<br>
      Brampton, ON L6T&nbsp; 4K9
    </address>
  </section>

</body>
</html>
```